Business Card Design for company

We want new business cards. We'd like something different-- yet still highly professional. Our tagline is Providing leadership, delivering success. Stock photos are ok, as long as they are relevant and look upscale.

Target Market(s)

Architecture/Business Management Consulting/Engineering Consulting

Contact Information for Business Card

dark gray background with pops of blue might be good, but you tell me. You're the designers. Rounded corners might be nice, but again, you tell me.

Font styles to use
Serif
Sans Serif

Colors
3276b5
5c5c5c
9d9d9d
fbfbfb

Requirements
Nice to have
• Something different, but still very professional.

```html
<!DOCTYPE html>
<html lang="en">
<head>
<meta charset="utf-8">
<title>Norvale Group — Business Cards</title>
<link rel="stylesheet" href="https://fonts.googleapis.com/css2?family=Montserrat:wght@500;600&family=Open+Sans:wght@400;600;700&display=swap">
<style>
  :root {
    --stage: #2b2b2d;
    --blue-light: #4ab4f0;
    --blue: #3276b5;
    --blue-deep: #2a5f98;
    --ink-gray: #5c5c5c;
    --steel: #4a4c50;
    --paper: #fbfbfb;
    --white: #ffffff;
  }
  * { box-sizing: border-box; margin: 0; padding: 0; }
  html, body {
    width: 1200px; height: 885px; overflow: hidden;
    background: var(--stage);
  }
  .canvas { position: relative; width: 1200px; height: 885px; }

  .card {
    position: absolute;
    width: 580px; height: 330px;
    box-shadow: 0 14px 30px rgba(0,0,0,.45);
    overflow: hidden;
  }

  /* Front */
  .card-front {
    left: 70px; top: 80px;
    background: linear-gradient(135deg, var(--blue-light) 0%, var(--blue) 45%, var(--blue-deep) 100%);
    color: var(--white);
    text-align: center;
  }
  .front-name {
    position: absolute; left: 0; right: 0; top: 112px;
    font-family: "Montserrat", sans-serif;
    font-weight: 600; font-size: 58px; letter-spacing: 2px;
  }
  .front-tagline {
    position: absolute; left: 0; right: 0; bottom: 34px;
    font-family: "Open Sans", sans-serif;
    font-size: 15px; letter-spacing: .3px;
  }
  .front-tagline .dot {
    display: inline-block; width: 6px; height: 6px; border-radius: 50%;
    background: var(--white); margin: 0 8px; vertical-align: middle;
  }

  /* Back */
  .card-back {
    left: 550px; top: 475px;
    background: var(--paper);
  }
  .edge-bar {
    position: absolute; left: 0; top: 165px; width: 16px; bottom: 0;
    background: var(--steel);
  }
  .back-name {
    position: absolute; left: 56px; top: 190px;
    font-family: "Montserrat", sans-serif;
    font-weight: 600;
    color: var(--blue-deep);
    line-height: 1;
  }
  .back-name .name-main { display: block; font-size: 44px; letter-spacing: 1px; }
  .back-name .name-sub  { display: block; font-size: 19px; letter-spacing: 9px; margin-top: 8px; }
  .contact-panel {
    position: absolute; right: 0; top: 40px;
    width: 250px; height: 178px;
    background: var(--blue);
    color: var(--white);
    font-family: "Open Sans", sans-serif;
    padding: 14px 14px 0 20px;
  }
  .person-name { font-weight: 700; font-size: 17px; line-height: 1.05; }
  .person-role { font-size: 12px; text-transform: uppercase; margin-bottom: 6px; }
  .address { font-size: 12px; line-height: 1.3; margin-bottom: 4px; padding-left: 18px; }
  .contact-list { list-style: none; font-size: 12px; line-height: 1.35; }
  .contact-list li { display: flex; align-items: center; gap: 6px; }
  .contact-list svg { width: 12px; height: 12px; flex: none; }
</style>
</head>
<body>
<main class="canvas">

  <section class="card card-front" aria-label="Card front">
    <div class="front-name">NORVALE</div>
    <p class="front-tagline">Providing leadership<span class="dot"></span>delivering success</p>
  </section>

  <section class="card card-back" aria-label="Card back">
    <div class="edge-bar"></div>
    <div class="back-name">
      <span class="name-main">NORVALE</span>
      <span class="name-sub">GROUP</span>
    </div>

    <div class="contact-panel">
      <div class="person-name">ALEX MARLOW</div>
      <div class="person-role">President</div>
      <div class="address">1420 Harbor View Lane<br>Cedar Grove, NY 10512</div>
      <ul class="contact-list">
        <li>
          <svg viewBox="0 0 12 12" fill="#fff"><path d="M2 1.5l2 0 1 2.5-1.2 1a6 6 0 0 0 3.2 3.2l1-1.2 2.5 1v2a1 1 0 0 1-1 1A9 9 0 0 1 1 2.5a1 1 0 0 1 1-1z"/></svg>
          555 0142 7731
        </li>
        <li>
          <svg viewBox="0 0 12 12" fill="none" stroke="#fff" stroke-width="1.3"><rect x="3" y="1" width="6" height="10" rx="1"/><line x1="5" y1="9" x2="7" y2="9"/></svg>
          555 0187 3364
        </li>
        <li>
          <svg viewBox="0 0 12 12" fill="#fff"><rect x="3" y="1" width="6" height="3"/><rect x="1" y="4.5" width="10" height="5" rx="1"/><rect x="3" y="8" width="6" height="3" fill="#fff" stroke="#3276b5" stroke-width=".6"/></svg>
          555 0129 4408
        </li>
        <li>
          <svg viewBox="0 0 12 12" fill="none" stroke="#fff" stroke-width="1.2"><rect x="1" y="2.5" width="10" height="7"/><path d="M1 2.5l5 4 5-4"/></svg>
          alex@norvalegroup.com
        </li>
        <li>
          <svg viewBox="0 0 12 12" fill="none" stroke="#fff" stroke-width="1.1"><circle cx="6" cy="6" r="5"/><ellipse cx="6" cy="6" rx="2.2" ry="5"/><line x1="1" y1="6" x2="11" y2="6"/></svg>
          www.norvalegroup.com
        </li>
      </ul>
    </div>
  </section>

</main>
</body>
</html>
```